Business Card Design Project

Business card based on attached logo

Todd Merrick
Todd@lorvantest.com
877-514-9073 ext. 318
Www.LorvanTest.com

Industry/Entity Type

Business

```html
<!DOCTYPE html>
<html lang="en">
<head>
<meta charset="utf-8">
<title>LorvanTest Business Cards</title>
<link rel="stylesheet" href="https://fonts.googleapis.com/css2?family=Arimo:wght@400;700&display=swap">
<style>
  :root {
    --red: #ec1c24;
    --ink: #231f20;
    --paper: #ffffff;
    --mist-light: #f6f6f7;
    --mist-dark: #dcdddf;
    --backdrop: #e7e5e2;
  }
  * { box-sizing: border-box; margin: 0; padding: 0; }
  html, body {
    width: 1200px; height: 715px; overflow: hidden;
    background: var(--backdrop);
    font-family: "Arimo", Arial, sans-serif;
  }
  .sheet { position: relative; width: 1200px; height: 715px; }
  .card {
    position: absolute; width: 505px; height: 288px; overflow: hidden;
    box-shadow: 0 2px 6px rgba(0,0,0,0.25);
  }
  .card--front { left: 55px; top: 37px; background: radial-gradient(ellipse at 50% 30%, var(--mist-light), var(--mist-dark)); }
  .card--white { left: 623px; top: 37px; background: var(--paper); }
  .card--red   { left: 51px;  top: 379px; background: var(--red); }
  .card--black { left: 629px; top: 381px; background: var(--ink); }

  .brand {
    position: absolute; left: 0; right: 0; top: 62px;
    display: flex; justify-content: center; align-items: center; gap: 12px;
  }
  .brand__name { font-weight: 700; font-size: 50px; letter-spacing: -1px; color: var(--ink); }
  .brand__mark { width: 26px; height: 26px; background: var(--red); }

  .front-band { position: absolute; left: 0; top: 0; width: 505px; height: 288px; }
  .holder {
    position: absolute; left: 92px; top: 247px; transform: translateY(-50%);
    color: var(--paper); font-size: 19px; letter-spacing: 0.6px; white-space: nowrap;
  }
  .divider { position: absolute; left: 229px; top: 222px; width: 2px; height: 50px; background: var(--paper); border-radius: 1px; }
  .contact { position: absolute; left: 245px; top: 214px; list-style: none; color: var(--paper); font-size: 13.5px; white-space: nowrap; }
  .contact li { display: flex; align-items: center; gap: 6px; height: 22px; }
  .contact svg { width: 11px; height: 11px; flex: none; }

  .back-brand {
    position: absolute; left: 0; right: 0; top: 88px;
    display: flex; justify-content: center; align-items: center; gap: 14px;
    font-weight: 700; font-size: 56px; letter-spacing: -1px;
  }
  .back-brand__mark { width: 30px; height: 30px; }
  .card--white .back-brand { color: var(--red); }
  .card--white .back-brand__mark { background: var(--red); }
  .card--red .back-brand, .card--black .back-brand { color: var(--paper); }
  .card--red .back-brand__mark, .card--black .back-brand__mark { background: var(--paper); }

  .web {
    position: absolute; left: 0; right: 0; bottom: 17px; text-align: center;
    font-size: 16px; letter-spacing: 3px;
  }
  .card--white .web { color: var(--ink); }
  .card--red .web, .card--black .web { color: var(--paper); }
</style>
</head>
<body>
<main class="sheet">

  <section class="card card--front">
    <div class="brand">
      <span class="brand__name">LorvanTest</span>
      <span class="brand__mark"></span>
    </div>
    <svg class="front-band" viewBox="0 0 505 288" preserveAspectRatio="none" aria-hidden="true">
      <path d="M0 234 Q252 126 505 234 L505 288 L0 288 Z" fill="var(--ink)"/>
      <path d="M0 240 Q252 142 505 240 L505 288 L0 288 Z" fill="var(--paper)"/>
      <path d="M0 243 Q252 145 505 243 L505 288 L0 288 Z" fill="var(--red)"/>
    </svg>
    <div class="holder">Todd Merrick</div>
    <div class="divider"></div>
    <ul class="contact">
      <li>
        <svg viewBox="0 0 12 12"><path d="M3 1 L5 3.5 L4 5 Q5 7 7 8 L8.5 7 L11 9 L9.5 11 Q4 10.5 1 3 Z" fill="var(--paper)"/></svg>
        877-514-9073 ext. 318
      </li>
      <li>
        <svg viewBox="0 0 12 12"><rect x="1" y="3" width="10" height="7" fill="var(--paper)"/><path d="M1 3 L6 7 L11 3" fill="none" stroke="var(--red)" stroke-width="1"/></svg>
        Todd@lorvantest.com
      </li>
      <li>
        <svg viewBox="0 0 12 12"><circle cx="6" cy="6" r="5" fill="none" stroke="var(--paper)" stroke-width="1.2"/><ellipse cx="6" cy="6" rx="2" ry="5" fill="none" stroke="var(--paper)" stroke-width="1"/><line x1="1" y1="6" x2="11" y2="6" stroke="var(--paper)" stroke-width="1"/></svg>
        www.LorvanTest.com
      </li>
    </ul>
  </section>

  <section class="card card--white">
    <div class="back-brand"><span>LorvanTest</span><span class="back-brand__mark"></span></div>
    <div class="web">www.LorvanTest.com</div>
  </section>

  <section class="card card--red">
    <div class="back-brand"><span>LorvanTest</span><span class="back-brand__mark"></span></div>
    <div class="web">www.LorvanTest.com</div>
  </section>

  <section class="card card--black">
    <div class="back-brand"><span>LorvanTest</span><span class="back-brand__mark"></span></div>
    <div class="web">www.LorvanTest.com</div>
  </section>

</main>
</body>
</html>
```